Chartered Professional Accounting Firm Needs a Business Card Design

We need a card design for an accounting firm based in Toronto, Ontario. The firm name is Pavel Ostrom Professional Corporation. The owner of the firm is a chartered professional accountant and a certified general accountant. Services of the firm include 60% tax preparation and consulting and 40% financial statements for corporation year-end. We would like a modern design. The color could be black, white, gray, blue or other color to bring more confidence to clients. The logo of the firm should be included in the design. Thanks

Name: Pavel Ostrom, CPA, CGA Address: 47 Maple Crest Rd. Richmond Hill, ON L7K 3B5 Telephone: (416) 562-3907 Fax:(416) 734-2165 Email: pavel@pavelostrom-example.ca

Accounting

```html
<!DOCTYPE html>
<html lang="en">
<head>
<meta charset="utf-8">
<title>Pavel Ostrom Professional Corporation – Business Card</title>
<link href="https://fonts.googleapis.com/css2?family=Crimson+Pro:wght@400;600&display=swap" rel="stylesheet">
<style>
  :root {
    --backdrop: #dcd9d3;
    --card: #ededed;
    --brand-blue: #2e3192;
    --band-grey: #8a8a8a;
    --text-grey: #9a9a9a;
    --icon-grey: #7d7d7d;
    --white: #ffffff;
  }
  * { box-sizing: border-box; margin: 0; padding: 0; }
  html, body { width: 1200px; height: 800px; overflow: hidden; }
  body {
    background: var(--backdrop);
    font-family: "Crimson Pro", Georgia, serif;
    position: relative;
  }
  .card {
    position: absolute;
    top: 245px;
    width: 540px;
    height: 309px;
    background: var(--card);
    box-shadow: 0 6px 18px rgba(0,0,0,0.18);
  }
  .card--front { left: 40px; }
  .card--back { left: 620px; }

  /* Front */
  .front-mark {
    position: absolute;
    inset: 0;
    display: flex;
    align-items: center;
    justify-content: center;
    gap: 16px;
  }
  .front-mark__square {
    width: 46px; height: 46px;
    background: var(--brand-blue);
  }
  .front-mark__name {
    color: var(--brand-blue);
    font-weight: 600;
    font-size: 30px;
    letter-spacing: 1px;
    text-transform: uppercase;
  }

  /* Back */
  .firm {
    position: absolute;
    left: 34px; top: 34px;
    display: flex;
    align-items: flex-start;
    gap: 14px;
  }
  .firm__square {
    width: 38px; height: 38px;
    background: var(--brand-blue);
    margin-top: 4px;
  }
  .firm__name {
    color: var(--brand-blue);
    font-weight: 600;
    text-transform: uppercase;
    line-height: 1.02;
  }
  .firm__name-main { display: block; font-size: 30px; letter-spacing: 0.5px; }
  .firm__name-sub { display: block; font-size: 15px; letter-spacing: 0.6px; }
  .firm__credentials {
    margin-top: 3px;
    color: var(--text-grey);
    font-size: 11.5px;
    letter-spacing: 1.1px;
    text-transform: uppercase;
    line-height: 1.15;
  }

  .name-band {
    position: absolute;
    left: 0; right: 0;
    top: 142px;
    height: 36px;
    background: var(--band-grey);
    display: flex;
    align-items: center;
    padding-left: 34px;
    color: var(--white);
  }
  .name-band__person { font-size: 21px; letter-spacing: 1px; text-transform: uppercase; }
  .name-band__divider {
    width: 1px; height: 22px;
    background: rgba(255,255,255,0.7);
    margin: 0 12px;
  }
  .name-band__title { font-size: 14px; letter-spacing: 0.5px; }

  .address {
    position: absolute;
    left: 58px; top: 192px;
    color: var(--brand-blue);
    font-size: 15.5px;
  }
  .contact-list {
    position: absolute;
    list-style: none;
    color: var(--brand-blue);
    font-size: 15.5px;
  }
  .contact-list--phones { left: 58px; top: 226px; }
  .contact-list--online { left: 300px; top: 226px; }
  .contact-list li {
    display: flex;
    align-items: center;
    gap: 10px;
    height: 24px;
  }
  .contact-list svg { width: 16px; height: 16px; flex: none; }
</style>
</head>
<body>

  <section class="card card--front" aria-label="Card front">
    <div class="front-mark">
      <span class="front-mark__square"></span>
      <span class="front-mark__name">Pavel Ostrom</span>
    </div>
  </section>

  <section class="card card--back" aria-label="Card back">
    <div class="firm">
      <span class="firm__square"></span>
      <div>
        <p class="firm__name">
          <span class="firm__name-main">Pavel Ostrom</span>
          <span class="firm__name-sub">Professional Corporation</span>
        </p>
        <p class="firm__credentials">Chartered Professional Accountant<br>Certified General Accountant</p>
      </div>
    </div>

    <div class="name-band">
      <span class="name-band__person">Pavel Ostrom</span>
      <span class="name-band__divider"></span>
      <span class="name-band__title">CPA, CGA</span>
    </div>

    <p class="address">47 Maple Crest Rd. Richmond Hill, ON L7K 3B5</p>

    <ul class="contact-list contact-list--phones">
      <li>
        <svg viewBox="0 0 16 16" aria-label="Telephone" role="img">
          <path d="M2 6c0-2 2-3 6-3s6 1 6 3l-3 1-1-2H6L5 7z" fill="var(--icon-grey)"/>
          <rect x="3" y="8" width="10" height="6" rx="1" fill="var(--icon-grey)"/>
        </svg>
        <span>(416) 562-3907</span>
      </li>
      <li>
        <svg viewBox="0 0 16 16" aria-label="Fax" role="img">
          <rect x="4" y="1" width="8" height="5" fill="none" stroke="var(--icon-grey)" stroke-width="1.4"/>
          <rect x="1" y="6" width="14" height="6" rx="1" fill="var(--icon-grey)"/>
          <rect x="4" y="10" width="8" height="5" fill="var(--card)" stroke="var(--icon-grey)" stroke-width="1.2"/>
        </svg>
        <span>(416) 734-2165</span>
      </li>
    </ul>

    <ul class="contact-list contact-list--online">
      <li>
        <svg viewBox="0 0 16 16" aria-label="Website" role="img">
          <rect x="1.5" y="2" width="13" height="9" fill="none" stroke="var(--icon-grey)" stroke-width="1.4"/>
          <rect x="6" y="11" width="4" height="2" fill="var(--icon-grey)"/>
          <rect x="4" y="13" width="8" height="1.5" fill="var(--icon-grey)"/>
        </svg>
        <span>www.pavelostrom-example.ca</span>
      </li>
      <li>
        <svg viewBox="0 0 16 16" aria-label="Email" role="img">
          <rect x="1" y="3" width="14" height="10" fill="var(--icon-grey)"/>
          <path d="M1 3l7 6 7-6M1 13l5-5M15 13l-5-5" fill="none" stroke="var(--card)" stroke-width="1"/>
        </svg>
        <span>pavel@pavelostrom-example.ca</span>
      </li>
    </ul>
  </section>

</body>
</html>
```